Desktop and Networking Support Course 9.17.25

Important the ad should not be very busy with the text taking up the major part of the ad .. please do not make the text so big that it takes up most of the ad..
Flyer Design Brief for Graphic Artist
also i am looking for something unique or creative that it will stand out .
Size & Layout:
Full Page with Bleed: 8” x 10.75” + 0.25” bleed on all sides.
Footer Space: Leave a 1-inch margin at the bottom for footer content (e.g., contact info, logo, or call-to-action).
Target Audience:
College-age students (around 24 years old)
Located in the USA
Interested in creative, professional, and career-building opportunities
Purpose:
To attract students to enroll in a college program
Flyer should be eye-catching, unique, and creative
Text must be clear and readable,
Design Style:
Use vector art, typography, or photography — your choice
If using photography, feature a white young professional USA citizen:
Wearing a white collared shirt
not with long hair
Creative Direction:
The flyer should stand out visually — something people would want to look at and keep
Showcase creativity and professionalism
Use bold colors, dynamic layout, or unexpected design elements to grab attention
Avoid clutter — keep the design balanced and clean
Text Suggestions (can be adjusted):
Footer,
please leave one inch on the bottom for the footer

```html
<!DOCTYPE html>
<html lang="en">
<head>
<meta charset="utf-8">
<title>Desktop &amp; Networking Support Course</title>
<link href="https://fonts.googleapis.com/css2?family=Fredoka:wght@500;600&family=Mulish:wght@800;900&family=Tinos:wght@700&display=swap" rel="stylesheet">
<style>
  :root {
    --coral: #ff5a4a;
    --orange: #ff8a3a;
    --amber: #fdaa35;
    --gold: #f7cc28;
    --white: #ffffff;
    --ink: #1f1f1f;
    --navy: #2b3a5e;
    --band-dark: rgba(95, 90, 90, 0.55);
    --band-light: rgba(235, 235, 235, 0.6);
  }
  * { margin: 0; padding: 0; box-sizing: border-box; }
  html, body { width: 907px; height: 1200px; overflow: hidden; background: #fff; }
  .flyer { position: relative; width: 907px; height: 1200px; overflow: hidden; }

  .hero-photo {
    position: absolute; left: 0; top: 0; width: 907px; height: 1094px;
    background:
      radial-gradient(ellipse 260px 420px at 330px 720px, rgba(245,243,240,0.9), rgba(245,243,240,0) 70%),
      radial-gradient(ellipse 180px 300px at 130px 800px, rgba(236,232,228,0.85), rgba(236,232,228,0) 70%),
      linear-gradient(90deg, #8d8682 0%, #a8a29d 25%, #6e5f56 55%, #3b2a22 75%, #4a3a32 100%);
  }
  .hero-photo::after {
    content: ""; position: absolute; left: 0; right: 0; bottom: 0; height: 320px;
    background: linear-gradient(180deg, rgba(200,195,190,0) 0%, rgba(215,210,205,0.55) 100%);
  }

  .tagline {
    position: absolute; left: 0; width: 907px; top: 44px; padding-left: 163px;
    font-family: "Tinos", serif; font-weight: 700; font-size: 34px;
    letter-spacing: 2.4px; color: var(--white);
  }

  .title { position: absolute; right: 49px; top: 104px; text-align: right;
    font-family: "Mulish", sans-serif; font-weight: 900; font-size: 80px;
    line-height: 93px; letter-spacing: 0.5px; }
  .title span { display: block; }
  .title .t1 { color: var(--coral); }
  .title .t2 { background: linear-gradient(90deg, var(--orange), #ff7c38); -webkit-background-clip: text; background-clip: text; color: transparent; }
  .title .t3 { color: var(--amber); }
  .title .t4 { color: var(--gold); }

  .highlights { position: absolute; left: 0; top: 0; }
  .highlight {
    position: absolute; left: 400px; width: 463px;
    font-family: "Fredoka", sans-serif; font-weight: 600; color: var(--coral);
    font-size: 23px; line-height: 1; white-space: nowrap;
  }
  .highlight::before {
    content: ""; position: absolute; left: 202px; right: 0; top: -10px; bottom: -10px;
    background: linear-gradient(90deg, rgba(95,90,90,0), var(--band-dark) 20%, var(--band-dark) 85%, rgba(95,90,90,0));
    z-index: -1;
  }
  .highlights { z-index: 1; }
  .hl-1 { top: 555px; padding-left: 8px; }
  .hl-2 { top: 607px; padding-left: 8px; }
  .hl-3 { top: 652px; padding-left: 8px; }
  .hl-3 small { display: block; font-size: 14px; margin-top: 2px; }
  .hl-3::before { bottom: -6px; }

  .features { position: absolute; right: 49px; top: 843px; width: 270px; text-align: right;
    font-family: "Fredoka", sans-serif; font-weight: 500; font-size: 24px; line-height: 27px; color: var(--white); }
  .feature { padding: 2px 0 6px; }
  .feature + .feature { border-top: 3px solid var(--coral); padding-top: 6px; }

  .delivery {
    position: absolute; left: 0; top: 1027px; width: 907px; height: 56px;
    background: linear-gradient(90deg, rgba(235,235,235,0.35), var(--band-light) 40%, var(--band-light) 60%, rgba(235,235,235,0.35));
    font-family: "Tinos", serif; font-weight: 700; font-size: 21px; letter-spacing: 2px;
    color: var(--ink); text-align: center; line-height: 27px; padding-top: 2px;
  }

  .footer { position: absolute; left: 0; top: 1094px; width: 907px; height: 106px; background: var(--navy); }
</style>
</head>
<body>
  <div class="flyer">
    <div class="hero-photo" role="img" aria-label="Two young professionals in white collared shirts standing in a softly lit modern office corridor"></div>

    <p class="tagline">Your Career Is Just a Click Away</p>

    <h1 class="title">
      <span class="t1">DESKTOP</span>
      <span class="t2">&amp; NETWORKING</span>
      <span class="t3">SUPPORT</span>
      <span class="t4">COURSE</span>
    </h1>

    <div class="highlights">
      <p class="highlight hl-1">Master Fenestra Operating Systems</p>
      <p class="highlight hl-2">90% Employment Rat - Class of 2024</p>
      <p class="highlight hl-3">Prepare for 3 of the Top 10 Tech Jobs<small>“National Career Review 2025”</small></p>
    </div>

    <div class="features">
      <p class="feature">Hands-On Desktop<br>&amp; Network Training</p>
      <p class="feature">Real-World<br>Troubleshooting Skills</p>
      <p class="feature">Ready for IT Jobs</p>
    </div>

    <div class="delivery">
      <p>In-Person and Remote Options</p>
      <p>Partial Scholarships Offered</p>
    </div>

    <div class="footer"></div>
  </div>
</body>
</html>
```